Brivane Management

We need a web design for a new consulting company, with clients all over the world. The company provides management consulting to the travel industry.

Logo files are attached.

Website must look very corporate and be responsive in design.

Management Consulting

```html
<!DOCTYPE html>
<html lang="en">
<head>
<meta charset="utf-8">
<title>Brivane Management — Strategy Management</title>
<link href="https://fonts.googleapis.com/css2?family=Open+Sans:wght@400;600;700&family=PT+Serif:wght@400;700&family=Oswald:wght@500&display=swap" rel="stylesheet">
<style>
:root{
  --blue:#1f7bc8;
  --blue-dark:#11579b;
  --blue-deep:#0b3f73;
  --green:#6aa842;
  --ink:#2d2d2d;
  --muted:#666;
  --band:#e8e9eb;
  --line:#d5d7da;
  --white:#fff;
}
*{box-sizing:border-box;margin:0;padding:0}
html,body{width:756px;height:1200px;overflow:hidden;background:var(--white)}
body{font-family:"Open Sans",Arial,sans-serif;color:var(--ink);position:relative}
.site-header{height:76px;display:flex;align-items:center;justify-content:space-between;padding:0 34px}
.brand{display:flex;align-items:center;gap:8px}
.brand-dot{width:26px;height:26px;border-radius:50%;background:var(--blue)}
.brand-name{font-family:"Open Sans",Arial,sans-serif;font-weight:700;font-size:17px;color:var(--blue-dark);letter-spacing:.5px}
.main-nav{display:flex;gap:30px;font-size:9px;font-weight:600;letter-spacing:.6px;color:#444}
.hero{position:relative;height:289px;background:linear-gradient(180deg,#2a5fa6 0%,#6b9fd8 40%,#d9e6f2 72%,#b9c9da 100%)}
.hero-tagline{position:absolute;right:16px;top:110px;width:270px;background:rgba(8,22,45,.82);color:var(--white);font-family:"Oswald",Arial,sans-serif;font-size:17px;line-height:1.35;padding:12px 16px;letter-spacing:.4px}
.welcome{text-align:center;padding:22px 60px 0;height:215px}
.section-title{font-family:"PT Serif",Georgia,serif;font-size:23px;letter-spacing:1.5px;color:#333;font-weight:400}
.section-sub{font-size:8.5px;font-weight:700;color:var(--green);letter-spacing:1px;margin-top:2px;display:flex;align-items:center;justify-content:center;gap:10px}
.section-sub::before,.section-sub::after{content:"";width:40px;height:1px;background:var(--line)}
.welcome p{font-size:8.5px;line-height:1.6;color:var(--muted);margin-top:12px;text-align:left}
.welcome p strong{color:#333}
.btn{display:inline-block;background:var(--blue);color:var(--white);font-size:7.5px;font-weight:700;padding:5px 10px;letter-spacing:.4px}
.welcome .btn{margin-top:12px}
.services{background:var(--band);height:240px;display:flex;gap:14px;padding:18px 38px 0}
.service-card{width:158px;text-align:center}
.service-photo{height:82px;border:3px solid var(--white)}
.service-card h3{font-size:11.5px;font-weight:600;margin-top:9px;color:#222}
.service-card p{font-size:7.5px;line-height:1.5;color:var(--muted);margin:5px 10px 7px}
.testimonials{text-align:center;padding-top:22px;height:196px}
.quotes{display:flex;gap:24px;padding:18px 38px 0}
.quote{flex:1;text-align:left}
.quote-box{border:1px solid var(--line);display:flex;gap:12px;padding:10px;align-items:center}
.avatar{width:46px;height:46px;border-radius:50%;flex:none;background:linear-gradient(135deg,#c9d3dd,#8f9fb0)}
.quote-box p{font-size:7.5px;line-height:1.55;color:var(--muted)}
.quote-name{font-size:8.5px;font-weight:600;margin:8px 0 0 14px}
.site-footer{position:absolute;left:0;top:1018px;width:756px;height:162px;background:var(--blue-dark);color:var(--white);display:flex;gap:18px;padding:18px 34px 0}
.footer-col{flex:1;font-size:8px;line-height:1.6}
.footer-col h4{font-size:11px;font-weight:600;margin-bottom:8px}
.footer-col li{list-style:none;display:flex;align-items:center;gap:6px;margin-bottom:3px}
.footer-col li::before{content:"›";font-weight:700}
.footer-col .plain li::before{content:none}
.icon-dot{width:14px;height:14px;border-radius:50%;background:var(--white);flex:none}
.signup-input{height:18px;background:var(--white);margin:6px 0 6px}
.copyright{position:absolute;left:0;top:1180px;width:756px;height:20px;background:var(--blue-deep);color:#cfe0f2;font-size:7.5px;text-align:center;line-height:20px}
</style>
</head>
<body>
<header class="site-header">
  <div class="brand"><span class="brand-dot"></span><span class="brand-name">BRIVANE MANAGEMENT</span></div>
  <nav class="main-nav"><span>HOME</span><span>ABOUT US</span><span>SERVICES</span><span>CONTACT US</span></nav>
</header>

<section class="hero" role="img" aria-label="Collage of world landmarks under a blue sky with an airliner flying overhead">
  <div class="hero-tagline">WE PROVIDES MANAGEMENT<br>CONSULTING TO THE TRAVEL INDUSTRY.</div>
</section>

<section class="welcome">
  <h1 class="section-title">WELCOME BRIVANE</h1>
  <div class="section-sub">STRATEGY MANAGEMENT, INC.</div>
  <p><strong>Lorem ipsum dolor sit amet, consectetur adipisicing elit, sed do eiusmod tempor incididunt ut labore et dolore magna aliqua. Ut enim ad minim veniam.</strong><br>
  Duis aute irure dolor in reprehenderit in voluptate velit esse cillum dolore eu fugiat nulla pariatur. Excepteur sint occaecat cupidatat non proident, sunt in culpa qui officia deserunt mollit anim id est laborum. Sed ut perspiciatis unde omnis iste natus error sit voluptatem accusantium doloremque laudantium, totam rem aperiam, eaque ipsa quae ab illo inventore veritatis et quasi architecto beatae vitae dicta sunt explicabo. Nemo enim ipsam voluptatem quia voluptas sit aspernatur aut odit aut fugit.</p>
  <span class="btn">READ MORE</span>
</section>

<section class="services">
  <article class="service-card">
    <div class="service-photo" role="img" aria-label="Business people shaking hands" style="background:linear-gradient(160deg,#dfe5ec,#7d8ea3)"></div>
    <h3>Account Management</h3>
    <p>Duis aute irure dolor in dolor voluptate velit esse.</p>
    <span class="btn">READ MORE</span>
  </article>
  <article class="service-card">
    <div class="service-photo" role="img" aria-label="Team meeting around a table" style="background:linear-gradient(160deg,#e7e1d8,#8b8a8c)"></div>
    <h3>Traveller Tools</h3>
    <p>Duis aute irure dolor in dolor voluptate velit esse.</p>
    <span class="btn">READ MORE</span>
  </article>
  <article class="service-card">
    <div class="service-photo" role="img" aria-label="Calculator and financial papers" style="background:linear-gradient(160deg,#e9eef3,#6d8cb0)"></div>
    <h3>Expense Management</h3>
    <p>Duis aute irure dolor in dolor voluptate velit esse.</p>
    <span class="btn">READ MORE</span>
  </article>
  <article class="service-card">
    <div class="service-photo" role="img" aria-label="Traveller with luggage in an airport terminal" style="background:linear-gradient(160deg,#e3e8ee,#5f6f84)"></div>
    <h3>Travel Programs</h3>
    <p>Duis aute irure dolor in dolor voluptate velit esse.</p>
    <span class="btn">READ MORE</span>
  </article>
</section>

<section class="testimonials">
  <h2 class="section-title">CLIENT TESTIMONIALS</h2>
  <div class="section-sub">NEQUE PORRO QUISQUAM MOLIREM</div>
  <div class="quotes">
    <div class="quote">
      <div class="quote-box"><span class="avatar" role="img" aria-label="Client portrait"></span>
        <p>Lorem ipsum dolor sit amet, consectetur adipisicing elit, sed do eiusmod tempor incididunt ut labore et dolore magna aliqua. Ut enim ad minim veniam quis nostrud exercitation ullamco laboris.</p></div>
      <div class="quote-name">Mr. Client Name</div>
    </div>
    <div class="quote">
      <div class="quote-box"><span class="avatar" role="img" aria-label="Client portrait"></span>
        <p>Lorem ipsum dolor sit amet, consectetur adipisicing elit, sed do eiusmod tempor incididunt ut labore et dolore magna aliqua. Ut enim ad minim veniam quis nostrud exercitation ullamco laboris.</p></div>
      <div class="quote-name">Mr. Client Name</div>
    </div>
  </div>
</section>

<footer class="site-footer">
  <div class="footer-col">
    <h4>Quick Links</h4>
    <ul><li>Home</li><li>About Us</li><li>Services</li><li>Contact Us</li></ul>
  </div>
  <div class="footer-col">
    <h4>Contact Information</h4>
    <ul class="plain">
      <li>BRIVANE<br>48 Harbour Lane, Suite 12<br>Port Ellis, CA 90210</li>
      <li>(555) 214 7380</li>
      <li>info@brivanemgmt.com</li>
    </ul>
  </div>
  <div class="footer-col">
    <h4>Newsletter Sign Up</h4>
    <div>Lorem ipsum dolor sit amet, sed do eiusmod tempor.</div>
    <div class="signup-input"></div>
    <span class="btn">SUBSCRIBE</span>
  </div>
  <div class="footer-col">
    <h4>Follow Us</h4>
    <ul class="plain">
      <li><span class="icon-dot"></span>Linkbook</li>
      <li><span class="icon-dot"></span>Chirpline</li>
      <li><span class="icon-dot"></span>Circleplus</li>
    </ul>
  </div>
</footer>
<div class="copyright">© 2014 Brivane. All rights reserved.</div>
</body>
</html>
```